Lantern Petals Website v.1 - attract floral shop franchisees

I need a simple information website for my new business. We are a franchisor of flower shops. The overall purpose of the website is to promote the company and the service, especially to potential franchisees and retailers. Only about 4 pages are required including homepage, About, For Supermarkets, For Franchisees, and Contact. No special functions are required except the site will have two separate inquiry forms that must be filled out online and submitted via automated email. Similarly, an email form should be linked from the Contact page. I have a logo and business cards designed by ArtMingle, and I would like the site to have a consistent color scheme and style. The key to design will be to express the joy and love associated with flowers and floral bouquets.
IMPORTANT - I will be exporting the website design to Wordpress CMS in a site hosted by HostNimbus. For smooth integration into WordPress hosted by HostNimbus, the designer should build the site using a WordPress-friendly format. Ideally, they should use HTML, CSS, and PHP. Creating a custom theme or using a page builder that exports to WordPress-compatible files is best. This ensures the site can be easily imported and managed within WordPress.

Target Market(s)

Potential franchisees (existing florists or creative types who might like to own a floral business) and supermarkets who might want us to run their floral department

Industry/Entity Type

Floral retailing

Requirements
Must have
• A brand theme that is beautiful, consistent throughout and builds on the logo design
Nice to have
• Show gender and ethnic diversity in customers and florists. Pictures of happy florists (for franchisees) and pictures of amazing floral department displays (for supermarkets)

```html
<!DOCTYPE html>
<html lang="en">
<head>
<meta charset="utf-8">
<title>Lantern Petals</title>
<link href="https://fonts.googleapis.com/css2?family=Playfair+Display:wght@700&family=Roboto:wght@400;500;700&display=swap" rel="stylesheet">
<style>
:root{
  --orange:#f0961c;
  --green:#0f9a4a;
  --green-dark:#0b8a41;
  --ink:#2a2a2a;
  --body:#555;
  --grey-bg:#f3f3f3;
  --black:#000;
  --white:#fff;
}
*{box-sizing:border-box;margin:0;padding:0}
html,body{width:1200px;height:3526px;overflow:hidden}
body{position:relative;font-family:'Roboto',sans-serif;color:var(--body);background:var(--white)}
.abs{position:absolute}
.serif{font-family:'Playfair Display',serif;font-weight:700;color:var(--ink)}
.btn{position:absolute;display:flex;align-items:center;justify-content:center;gap:10px;height:47px;border-radius:24px;background:var(--orange);color:var(--white);font-size:15px;font-weight:700;text-transform:uppercase;letter-spacing:.2px}
.btn svg{width:15px;height:15px}
.brand{font-family:'Roboto',sans-serif;font-weight:700;color:var(--orange);display:flex;align-items:center;gap:10px}
.brand .dot{width:34px;height:34px;border-radius:50%;background:var(--orange)}
.social{width:36px;height:36px;border:2px solid var(--green);border-radius:50%}
/* header */
.header{left:0;top:0;width:1200px;height:106px;background:var(--white)}
.nav{top:70px;font-size:15px;color:var(--ink);font-weight:500}
.call-label{left:968px;top:13px;font-size:13px;color:#555}
.call-num{left:968px;top:32px;font-size:16px;font-weight:700;color:var(--ink)}
/* hero */
.hero-photo{left:0;top:106px;width:1200px;height:800px;background:linear-gradient(120deg,#c94b86 0%,#e8b7a5 30%,#d7c3b5 50%,#3d6fa8 65%,#e36f6a 85%,#b83a53 100%)}
.hero-box{left:287px;top:324px;width:626px;height:302px;background:rgba(40,40,40,.55)}
.hero-welcome{left:0;width:1200px;top:352px;text-align:center;font-size:42px;color:var(--white)}
.hero-title{left:0;width:1200px;top:408px;text-align:center;font-size:74px;color:var(--white)}
/* about */
.section-title{font-size:44px}
.about-text{left:109px;top:1066px;width:410px;font-size:15.5px;line-height:25.8px;text-align:justify}
.ph{position:absolute;border-radius:8px}
/* supermarkets */
.super-bg{left:0;top:1496px;width:1200px;height:511px;background:var(--grey-bg)}
.super-text{left:663px;top:1616px;width:428px;font-size:15.5px;line-height:27.4px;text-align:justify;color:#444}
/* contact band */
.contact-band{left:0;top:2007px;width:1200px;height:318px;background:var(--green)}
.contact-text{left:218px;top:2118px;width:764px;text-align:center;font-size:15.5px;line-height:26px;color:var(--white)}
/* franchisees */
.fr-text{left:110px;top:2530px;width:490px;font-size:15.5px;line-height:29.3px;text-align:justify;color:#444}
/* footer */
.footer{left:0;top:3060px;width:1200px;height:415px;background:var(--black)}
.f-head{font-size:14px;font-weight:700;color:var(--white);text-transform:uppercase}
.f-rule{width:40px;height:2px;background:var(--white)}
.f-link{font-size:14px;color:var(--white);display:flex;align-items:center;gap:12px}
.f-ico{width:26px;height:26px;border-radius:50%;background:#333;display:flex;align-items:center;justify-content:center}
.f-ico svg{width:13px;height:13px}
.copy{left:0;top:3475px;width:1200px;height:51px;background:var(--orange);color:var(--white);font-size:14px;display:flex;align-items:center;justify-content:center}
</style>
</head>
<body>

<!-- header -->
<div class="abs header"></div>
<div class="abs brand" style="left:110px;top:34px;font-size:30px"><span class="dot"></span>Lantern Petals</div>
<div class="abs social" style="left:825px;top:13px" aria-label="Social profile"></div>
<div class="abs social" style="left:872px;top:13px" aria-label="Social profile"></div>
<div class="abs" style="left:925px;top:14px;width:34px;height:34px;border-radius:50%;background:var(--orange);display:flex;align-items:center;justify-content:center">
  <svg width="18" height="18" viewBox="0 0 24 24"><path fill="#fff" d="M6.6 10.8c1.4 2.8 3.8 5.1 6.6 6.6l2.2-2.2c.3-.3.7-.4 1-.2 1.1.4 2.3.6 3.6.6.6 0 1 .4 1 1V20c0 .6-.4 1-1 1C10.6 21 3 13.4 3 4c0-.6.4-1 1-1h3.5c.6 0 1 .4 1 1 0 1.3.2 2.5.6 3.6.1.3 0 .7-.2 1z"/></svg>
</div>
<div class="abs call-label">Call Us</div>
<div class="abs call-num">+ 1.555.010.2040</div>
<div class="abs nav" style="left:483px">HOME</div>
<div class="abs nav" style="left:566px">ABOUT</div>
<div class="abs nav" style="left:655px">FOR SUPERMARKETS</div>
<div class="abs nav" style="left:845px">FOR FRANCHISEES</div>
<div class="abs nav" style="left:1017px">CONTACT</div>

<!-- hero -->
<div class="abs hero-photo" role="img" aria-label="Smiling florist arranging a vase of flowers in a colourful flower shop"></div>
<div class="abs hero-box"></div>
<div class="abs serif hero-welcome" style="color:var(--white)">Welcome To</div>
<div class="abs serif hero-title" style="color:var(--white)">Lantern Petals</div>
<div class="btn" style="left:516px;top:538px;width:168px">Get Started
  <svg viewBox="0 0 16 16"><circle cx="8" cy="8" r="7" fill="#fff"/><path d="M6 4.5 9.5 8 6 11.5" stroke="#f0961c" stroke-width="2" fill="none"/></svg></div>
<svg class="abs" style="left:0;top:700px" width="1200" height="210" viewBox="0 0 1200 210" preserveAspectRatio="none">
  <path fill="#f0961c" d="M0,85 C200,35 450,80 700,140 C860,175 1020,150 1200,90 V210 H0Z"/>
  <path fill="#0f9a4a" d="M0,150 C200,75 450,105 700,152 C860,180 1020,160 1200,98 V210 H0Z"/>
  <path fill="#ffffff" d="M0,195 C200,100 450,115 700,160 C860,188 1020,170 1200,100 V210 H0Z"/>
</svg>

<!-- about -->
<div class="abs serif section-title" style="left:109px;top:1003px">About Us</div>
<div class="abs about-text">Lantern Petals operates in partnership with Frostline Group, the leading franchisor of sushi stations and pre-packaged fruit &amp; vegetable departments to supermarkets across the United States and United Kingdom. Lantern Petals’ combination of floral and supermarket franchising expertise guarantees that consumers, franchisees and supermarket partners each receive exceptional service and value.</div>
<div class="btn" style="left:109px;top:1340px;width:168px">Learn More
  <svg viewBox="0 0 16 16"><circle cx="8" cy="8" r="7" fill="#fff"/><path d="M6 4.5 9.5 8 6 11.5" stroke="#f0961c" stroke-width="2" fill="none"/></svg></div>
<div class="ph" style="left:702px;top:977px;width:388px;height:370px;background:linear-gradient(135deg,#8a5a48,#c98a6e 45%,#5f7f4a 80%,#e0a24a)" role="img" aria-label="Two florists laughing while arranging bouquets in a shop"></div>
<div class="ph" style="left:611px;top:1137px;width:242px;height:250px;background:linear-gradient(160deg,#f4f4f4,#e6a6c3 45%,#e75fa7 85%);border:4px solid #fff" role="img" aria-label="Flower arrangement in a pink hat box"></div>

<!-- supermarkets -->
<div class="abs super-bg"></div>
<svg class="abs" style="left:0;top:1496px" width="635" height="511" viewBox="0 0 635 511" role="img" aria-label="Person holding a large bouquet of pink roses">
  <defs><linearGradient id="bq" x1="0" y1="0" x2="1" y2="1"><stop offset="0" stop-color="#e9e2d3"/><stop offset=".5" stop-color="#e79aa8"/><stop offset="1" stop-color="#8aa24c"/></linearGradient></defs>
  <polygon points="0,0 630,0 582,511 0,511" fill="url(#bq)"/>
  <polygon points="625,0 633,0 591,511 583,511" fill="#f0961c"/>
</svg>
<div class="abs serif section-title" style="left:663px;top:1552px;font-size:40px">For Supermarkets</div>
<div class="abs super-text">Lantern Petals works with some of the country’s largest and most progressive supermarkets to provide franchisee ownership and operation of their strategically important floral departments. Supermarkets find that Lantern Petals is able to improve their financial outcomes, provide attentive customer service and satisfaction, and lift the quality of the entire store environment.<br><span style="display:block;height:4px"></span>Lantern Petals works with some of the country’s largest and most progressive supermarkets to provide franchisee ownership and operation of their strategically important floral departments.</div>
<div class="btn" style="left:663px;top:1916px;width:168px">Learn More
  <svg viewBox="0 0 16 16"><circle cx="8" cy="8" r="7" fill="#fff"/><path d="M6 4.5 9.5 8 6 11.5" stroke="#f0961c" stroke-width="2" fill="none"/></svg></div>

<!-- contact band -->
<div class="abs contact-band"></div>
<div class="abs serif" style="left:0;width:1200px;top:2050px;text-align:center;font-size:42px;color:var(--white)">Contact Us</div>
<div class="abs contact-text">Lorem ipsum dolor sit ameted consectetur adipiscing elited sed do eiusmod tempor incididunt ut labore dolore magna aliqua Uted enim ad minim veniam, quis nostrud exercitation ullamco laboris nisi ut aliquip ex ea commodo consequat. Duis aute irure dolor in reprehenderit in voluptate velit esse cillum dolore</div>
<div class="btn" style="left:237px;top:2220px;width:331px">New Florist Franchise Inquiry
  <svg viewBox="0 0 16 16"><circle cx="8" cy="8" r="7" fill="#fff"/><path d="M6 4.5 9.5 8 6 11.5" stroke="#f0961c" stroke-width="2" fill="none"/></svg></div>
<div class="btn" style="left:580px;top:2219px;width:385px;height:49px;background:transparent;border:2px solid var(--white)">Professional Florist Franchise Inquiry
  <svg viewBox="0 0 16 16"><circle cx="8" cy="8" r="7" fill="#fff"/><path d="M6 4.5 9.5 8 6 11.5" stroke="#0f9a4a" stroke-width="2" fill="none"/></svg></div>

<!-- franchisees -->
<div class="abs serif section-title" style="left:110px;top:2470px">For Franchisees</div>
<div class="abs fr-text">Lantern Petals brings the best of professional florists and supermarkets together for the benefit of consumers. It supports a national network of owner-operator franchisees, who in many cases are multi-site professional florists, with comprehensive services to enhance franchise profitability. Lantern Petals works with some of the country’s largest and most progressive supermarkets to provide franchisee ownership and operation of their strategically important floral departments</div>
<div class="btn" style="left:110px;top:2790px;width:168px">Learn More
  <svg viewBox="0 0 16 16"><circle cx="8" cy="8" r="7" fill="#fff"/><path d="M6 4.5 9.5 8 6 11.5" stroke="#f0961c" stroke-width="2" fill="none"/></svg></div>
<div class="abs" style="left:662px;top:2444px;width:4px;height:464px;background:var(--orange)"></div>
<div class="abs" style="left:662px;top:2904px;width:538px;height:4px;background:#6fa03a"></div>
<div class="abs" style="left:678px;top:2428px;width:522px;height:460px;background:linear-gradient(150deg,#c9d6e2,#f4ece6 35%,#f1a78e 60%,#e88f86 75%,#8aa884)" role="img" aria-label="Hands holding a wrapped bouquet of peach roses and white flowers"></div>

<!-- footer -->
<svg class="abs" style="left:0;top:2960px" width="1200" height="110" viewBox="0 0 1200 110" preserveAspectRatio="none">
  <path fill="#0f9a4a" d="M0,90 C250,15 550,45 850,60 C1000,65 1120,35 1200,10 V110 H0Z"/>
  <path fill="#f0961c" d="M0,95 C250,25 550,60 850,80 C1000,90 1120,70 1200,45 V110 H0Z"/>
  <path fill="#000000" d="M0,100 C250,30 550,70 850,100 C1000,110 1120,95 1200,80 V110 H0Z"/>
</svg>
<div class="abs footer"></div>
<div class="abs brand" style="left:110px;top:3232px;font-size:30px"><span class="dot"></span>Lantern Petals</div>

<div class="abs f-head" style="left:372px;top:3202px">Quick Links</div>
<div class="abs f-rule" style="left:372px;top:3234px"></div>
<div class="abs" style="left:372px;top:3257px;display:flex;flex-direction:column;gap:12px">
  <div class="f-link"><span>»</span>Home</div>
  <div class="f-link"><span>»</span>About</div>
  <div class="f-link"><span>»</span>For Supermarkets</div>
  <div class="f-link"><span>»</span>For Franchisees</div>
  <div class="f-link"><span>»</span>Contact</div>
</div>

<div class="abs f-head" style="left:574px;top:3202px">Contact Us</div>
<div class="abs f-rule" style="left:574px;top:3234px"></div>
<div class="abs f-link" style="left:574px;top:3257px;font-size:16px;font-weight:700"><span class="f-ico"><svg viewBox="0 0 24 24"><path fill="#fff" d="M6.6 10.8c1.4 2.8 3.8 5.1 6.6 6.6l2.2-2.2c.3-.3.7-.4 1-.2 1.1.4 2.3.6 3.6.6.6 0 1 .4 1 1V20c0 .6-.4 1-1 1C10.6 21 3 13.4 3 4c0-.6.4-1 1-1h3.5c.6 0 1 .4 1 1 0 1.3.2 2.5.6 3.6.1.3 0 .7-.2 1z"/></svg></span>+ 1.555.010.2040</div>
<div class="abs f-link" style="left:574px;top:3301px;font-size:13px"><span class="f-ico"><svg viewBox="0 0 24 24"><path fill="#fff" d="M3 6h18v12H3z"/><path d="M3 6l9 7 9-7" stroke="#333" stroke-width="2" fill="none"/></svg></span>hello@lantern-petals.com</div>
<div class="abs f-link" style="left:574px;top:3348px;font-size:13px;line-height:16px"><span class="f-ico"><svg viewBox="0 0 24 24"><path fill="#fff" d="M12 2a7 7 0 0 0-7 7c0 5 7 13 7 13s7-8 7-13a7 7 0 0 0-7-7zm0 9.5A2.5 2.5 0 1 1 12 6.5a2.5 2.5 0 0 1 0 5z"/></svg></span><span>114 ERLorem ipsum dolor sit<br>ameted consectetur adip</span></div>
<div class="abs f-link" style="left:574px;top:3393px;font-size:13px;text-decoration:underline"><span class="f-ico"><svg viewBox="0 0 24 24"><path fill="#fff" d="M3 5l6-2 6 2 6-2v16l-6 2-6-2-6 2z"/></svg></span>View Other Locations</div>

<div class="abs f-head" style="left:832px;top:3202px">Subscribe Now</div>
<div class="abs f-rule" style="left:832px;top:3234px"></div>
<div class="abs" style="left:832px;top:3261px;width:260px;font-size:13px;line-height:19px;color:var(--white)">Sign up to our newsletter and stay up to date</div>
<div class="abs" style="left:832px;top:3318px;width:256px;height:46px;border-radius:23px;background:var(--white);display:flex;align-items:center;padding-left:24px;gap:12px;font-size:13px;color:#666;overflow:hidden">
  <svg width="13" height="13" viewBox="0 0 24 24"><path fill="#555" d="M3 6h18v12H3z"/><path d="M3 6l9 7 9-7" stroke="#fff" stroke-width="2" fill="none"/></svg>Email Address
  <span style="position:absolute;right:0;top:0;width:46px;height:46px;background:var(--green);display:flex;align-items:center;justify-content:center"><svg width="16" height="16" viewBox="0 0 24 24"><path fill="#fff" d="M2 11l20-9-9 20-2-8z"/></svg></span>
</div>
<div class="abs" style="left:832px;top:3386px;width:31px;height:31px;border-radius:50%;background:var(--white)" aria-label="Social profile"></div>
<div class="abs" style="left:873px;top:3386px;width:31px;height:31px;border-radius:50%;background:var(--white)" aria-label="Social profile"></div>

<div class="abs copy">© 2024 Lantern Petals. All Rights Reserved</div>
</body>
</html>
```